Email Signature Design

Please design an email signature, the below is an example of our current design;
___

HARCOURT ESTATE PARTNERS PTY LTD
DOMINIC FARRADAY
Licensed Strata and Community Manager

148 Calloway Street,
ULTIMO NSW 2007

P: 02.9374.6082 F: 9463.7820
Website: www.harcourtestate.com.au

This e-mail message and accompanying data may contain information that is confidential and private. If you are not the intended recipient, the use, dissemination, distribution or copying of this message or data is prohibited.

If you have received this e-mail in error please notify us immediately and delete all material pertaining to this e-mail. strata@harcourtestate.com.au

___

We would like to incorporate our logo and company colours, you can view the colours and feel of image at www.harcourtestate.com.au

Industry/Entity Type

It Company

Requirements
Must have
• use of logo and company colours (image)

```html
<!DOCTYPE html>
<html lang="en">
<head>
<meta charset="utf-8">
<title>Email Signature – Harcourt Estate Partners</title>
<link rel="stylesheet" href="https://fonts.googleapis.com/css2?family=Roboto:wght@400;700&display=swap">
<style>
  :root {
    --olive: #857f3d;
    --tan: #e0d0a7;
    --slate: #6d6d6e;
    --ink: #333333;
    --muted: #4a4a4a;
    --paper: #ffffff;
  }
  html, body {
    margin: 0;
    padding: 0;
    width: 1200px;
    height: 391px;
    overflow: hidden;
    background: var(--paper);
  }
  .signature {
    position: relative;
    width: 1200px;
    height: 391px;
    font-family: "Roboto", Arial, sans-serif;
    color: var(--ink);
  }
  .brand-square {
    position: absolute;
    left: 93px;
    top: 46px;
    width: 96px;
    height: 96px;
    background: var(--olive);
  }
  .brand-name {
    position: absolute;
    left: 93px;
    top: 150px;
    margin: 0;
    font-size: 19px;
    font-weight: 700;
    letter-spacing: 0.2px;
    color: var(--slate);
  }
  .person-name {
    position: absolute;
    left: 93px;
    top: 204px;
    margin: 0;
    font-size: 16.5px;
    font-weight: 700;
    color: var(--olive);
    letter-spacing: 0.2px;
  }
  .person-role {
    position: absolute;
    left: 93px;
    top: 231px;
    margin: 0;
    font-size: 17px;
    color: var(--ink);
  }
  .address {
    position: absolute;
    left: 428px;
    top: 201px;
    margin: 0;
    font-style: normal;
    font-size: 17px;
    line-height: 28px;
    color: var(--ink);
  }
  .contact {
    position: absolute;
    left: 764px;
    top: 201px;
    margin: 0;
    padding: 0;
    list-style: none;
    font-size: 18px;
    color: var(--ink);
  }
  .contact-row {
    display: flex;
    align-items: center;
    height: 29px;
  }
  .contact-item {
    display: inline-flex;
    align-items: center;
    margin-right: 14px;
  }
  .contact-badge {
    display: inline-flex;
    align-items: center;
    justify-content: center;
    width: 20px;
    height: 20px;
    border-radius: 50%;
    background: var(--olive);
    color: var(--paper);
    font-size: 14px;
    margin-right: 8px;
  }
  .divider {
    position: absolute;
    left: 93px;
    top: 260px;
    width: 1008px;
    height: 3px;
    display: flex;
  }
  .divider .tan { background: var(--tan); flex: 335; }
  .divider .olive { background: var(--olive); flex: 337; }
  .divider .slate { background: var(--slate); flex: 336; }
  .disclaimer {
    position: absolute;
    left: 93px;
    top: 271px;
    width: 1030px;
    font-size: 15.5px;
    line-height: 19px;
    color: var(--muted);
  }
  .disclaimer p { margin: 0 0 9px 0; }
</style>
</head>
<body>
  <div class="signature">
    <div class="brand-square" aria-hidden="true"></div>
    <p class="brand-name">HARCOURT ESTATE PARTNERS</p>

    <p class="person-name">DOMINIC FARRADAY</p>
    <p class="person-role">Licensed Strata and Community Manager</p>

    <address class="address">148 Calloway Street,<br>ULTIMO NSW 2007</address>

    <ul class="contact">
      <li class="contact-row">
        <span class="contact-item"><span class="contact-badge">P</span>02.9374.6082</span>
        <span class="contact-item"><span class="contact-badge">F</span>9463.7820</span>
      </li>
      <li class="contact-row">
        <span class="contact-item"><span class="contact-badge">W</span>www.harcourtestate.com.au</span>
      </li>
    </ul>

    <div class="divider" aria-hidden="true">
      <span class="tan"></span><span class="olive"></span><span class="slate"></span>
    </div>

    <div class="disclaimer">
      <p>This e-mail message and accompanying data may contain information that is confidential and private. If you are not the intended recipient, the use, dissemination, distribution or copying of this message or data is prohibited.</p>
      <p>If you have received this e-mail in error please notify us immediately and delete all material pertaining to this e-mail. strata@harcourtestate.com.au</p>
    </div>
  </div>
</body>
</html>
```